qoBureau Business Card Design Project

We need a business card design for qoBureau. qoBureau is an underwriting agency. Underwriting agencies act on behalf of insurers, to underwrite insurance. We will be operating in specialised classes of insurance initially and looking to expand from there. We would like to see designs that incorporate our logo colours as well as a contrasting stand out colour - also we'd like the logo itself to be embossed on the card.

Industry/Entity Type

Insurance

Requirements
Must have
• Logo on front
Nice to have
• Logo solely featured on back of card
Should not have
• Please do not use comic cans font :)

```html
<!DOCTYPE html>
<html lang="en">
<head>
<meta charset="utf-8">
<title>qoBureau Business Card</title>
<link rel="stylesheet" href="https://fonts.googleapis.com/css2?family=Roboto:wght@700&family=Tinos:wght@400;700&display=swap">
<style>
  :root {
    --page-bg: #e4e4e4;
    --card-deep: #2a58b8;
    --card-mid: #3b6fd0;
    --card-light: #5a8ee0;
    --mark-tone: #c9d8f0;
    --text-light: #dce7f8;
    --text-soft: #b9cdee;
    --ghost: rgba(200, 220, 250, 0.22);
  }
  * { margin: 0; padding: 0; box-sizing: border-box; }
  html, body {
    width: 1200px;
    height: 801px;
    overflow: hidden;
    background: var(--page-bg);
  }
  .sheet {
    position: relative;
    width: 1200px;
    height: 801px;
    display: flex;
    align-items: center;
    justify-content: center;
    gap: 40px;
  }
  .card {
    position: relative;
    width: 540px;
    height: 309px;
    border-radius: 4px;
    overflow: hidden;
    background: radial-gradient(ellipse at 50% 55%, var(--card-light) 0%, var(--card-mid) 45%, var(--card-deep) 100%);
    box-shadow: 0 6px 18px rgba(0, 0, 0, 0.18);
  }

  /* Front */
  .card-front .brand-dot {
    position: absolute;
    left: 50%;
    top: 62px;
    width: 84px;
    height: 84px;
    margin-left: -42px;
    border-radius: 50%;
    background: var(--mark-tone);
  }
  .card-front .brand-name {
    position: absolute;
    left: 0;
    right: 0;
    top: 162px;
    text-align: center;
    font-family: "Roboto", Arial, sans-serif;
    font-weight: 700;
    font-size: 76px;
    letter-spacing: -1px;
    color: var(--mark-tone);
    line-height: 1;
  }

  /* Back */
  .card-back .ghost-circle {
    position: absolute;
    left: 118px;
    top: 30px;
    width: 250px;
    height: 250px;
    border-radius: 50%;
    border: 14px solid var(--ghost);
  }
  .card-back .details {
    position: absolute;
    left: 190px;
    top: 58px;
    width: 230px;
    text-align: center;
    font-family: "Tinos", "Times New Roman", serif;
    color: var(--text-soft);
  }
  .details .person-name {
    font-weight: 700;
    font-size: 28px;
    color: var(--text-light);
    line-height: 1.1;
  }
  .details .job-title {
    font-size: 14px;
    margin-top: 2px;
  }
  .details .contact {
    list-style: none;
    margin-top: 26px;
    font-size: 13px;
    line-height: 1.3;
  }
</style>
</head>
<body>
  <main class="sheet">
    <section class="card card-front" aria-label="Card front">
      <div class="brand-dot"></div>
      <div class="brand-name">qoBureau</div>
    </section>

    <section class="card card-back" aria-label="Card back">
      <div class="ghost-circle"></div>
      <div class="details">
        <div class="person-name">Your Name</div>
        <div class="job-title">Job Title</div>
        <ul class="contact">
          <li>Company Name</li>
          <li>yourname@yourcompany.com</li>
          <li>123 Address Lane</li>
          <li>Mobile Number</li>
          <li>Website Address</li>
        </ul>
      </div>
    </section>
  </main>
</body>
</html>
```